Home Loan Introducer needs logo/business cards

We need a simple but classy logo for business cards and flyers. The business is a home loan referral business that is called an Introducer. The business name is "The Harborline".
I was thinking very simple and straight to the point on the front with "Home Loans" the only thing on the front with a nice background colour/s.
Then on the back, "The Harborline"
and "Quality Customer Service"
and "Email, text or call welcome"
and then my name, email address and phone number.
Updates
Thank you for all the designs :-)
Target Market(s)
Home buyers.
Home owners.
Investors.
Industry/Entity Type
Loan
Look and feel

```html
<!DOCTYPE html>
<html lang="en">
<head>
<meta charset="utf-8">
<title>The Harborline – Business Card Presentation</title>
<link href="https://fonts.googleapis.com/css2?family=Ubuntu:wght@400;500;700&family=Exo+2:wght@600&display=swap" rel="stylesheet">
<style>
  :root {
    --brand-blue: #0066b3;
    --brand-orange: #fbad36;
    --paper: #ffffff;
    --note-orange: #f7ab3c;
    --card-shadow: 4px 6px 8px rgba(0, 0, 0, 0.45);
  }
  * { margin: 0; padding: 0; box-sizing: border-box; }
  html, body { width: 1200px; height: 845px; overflow: hidden; background: var(--paper); }
  .sheet { position: relative; width: 1200px; height: 845px; font-family: "Ubuntu", sans-serif; }

  .card { position: absolute; box-shadow: var(--card-shadow); overflow: hidden; }

  /* Info side */
  .card--info { left: 32px; top: 44px; width: 604px; height: 369px; background: var(--brand-orange); }
  .card__top { position: absolute; left: 0; top: 0; width: 100%; height: 184px; background: var(--paper); }
  .brand-dot { position: absolute; left: 50%; top: 42px; width: 72px; height: 72px; margin-left: -36px; border-radius: 50%; background: var(--brand-blue); }
  .brand-name { position: absolute; left: 0; width: 100%; top: 145px; text-align: center; font-weight: 700; font-size: 25px; color: var(--brand-blue); letter-spacing: 0.3px; }
  .benefits { position: absolute; left: 0; width: 100%; top: 202px; list-style: none; text-align: center; color: var(--brand-blue); font-size: 16px; line-height: 23px; font-weight: 500; }
  .benefits li { display: flex; justify-content: center; align-items: center; gap: 3px; }
  .benefits svg { width: 18px; height: 18px; }
  .contact-name { position: absolute; left: 0; width: 100%; top: 263px; text-align: center; color: var(--brand-blue); font-size: 24px; font-weight: 500; }
  .contact-rule { position: absolute; left: 205px; top: 299px; width: 195px; height: 2px; background: var(--paper); }
  .contact-lines { position: absolute; left: 0; width: 100%; top: 304px; text-align: center; font-size: 10.5px; line-height: 14px; font-weight: 500; }
  .contact-lines .label { color: var(--paper); }
  .contact-lines .value { color: var(--brand-blue); }

  /* Front side */
  .card--front { left: 33px; top: 438px; width: 599px; height: 366px; background: var(--brand-blue); }
  .headline-bar { position: absolute; left: 38px; top: 140px; width: 523px; height: 86px; background: var(--brand-orange); border-radius: 8px; display: flex; justify-content: center; align-items: center; gap: 22px; font-family: "Ubuntu", sans-serif; font-weight: 500; font-size: 70px; letter-spacing: 1px; padding-top: 10px; }
  .headline-bar .word-home { color: var(--paper); }
  .headline-bar .word-loan { color: var(--brand-blue); }

  /* Presentation notes */
  .note { position: absolute; font-family: "Exo 2", sans-serif; font-weight: 600; color: var(--note-orange); font-size: 20px; line-height: 26px; }
  .note--example { left: 696px; top: 285px; text-transform: uppercase; }
  .note--spec { left: 673px; top: 432px; }
  .note--spec .spec-title { text-transform: uppercase; }
</style>
</head>
<body>
<main class="sheet">

  <section class="card card--info" aria-label="Card information side">
    <div class="card__top">
      <div class="brand-dot" aria-hidden="true"></div>
      <div class="brand-name">THE HARBORLINE</div>
    </div>
    <ul class="benefits">
      <li><svg viewBox="0 0 20 20" aria-hidden="true"><path d="M2 11 L7 17 L18 2" fill="none" stroke="#fff" stroke-width="3" stroke-linecap="round" stroke-linejoin="round"/></svg>Quality Customer Service</li>
      <li><svg viewBox="0 0 20 20" aria-hidden="true"><path d="M2 11 L7 17 L18 2" fill="none" stroke="#fff" stroke-width="3" stroke-linecap="round" stroke-linejoin="round"/></svg>Email, text or call welcome</li>
    </ul>
    <div class="contact-name">Dana Whitcombe</div>
    <div class="contact-rule"></div>
    <div class="contact-lines">
      <div><span class="label">Phone: </span><span class="value">+6390555017</span></div>
      <div><span class="label">Email: </span><span class="value">dana@harborline.example</span></div>
    </div>
  </section>

  <section class="card card--front" aria-label="Card front side">
    <div class="headline-bar">
      <span class="word-home">HOME</span><span class="word-loan">LOAN</span>
    </div>
  </section>

  <p class="note note--example">The name. email and phone number are<br>just example</p>
  <p class="note note--spec"><span class="spec-title">Double-sided business card</span><br>90mm x 55x Size<br>Info Centered</p>

</main>
</body>
</html>
```